Visitenkarten und Briefpapier
Zielgruppe
Planung und Realisierung von individuellen und wertbeständigen Kamin- und Ofenlösungen, sowie Fliesen- und Baddesign.
Aufgabenstellung
Wir benötigen ein möglichst schlichtes Design für Visitenkarten, bzw. Briefpapier. Für die Visitenkarten gerne auch Vorschläge mit Prägung, Ausstanzung oder mit Heißfolie. Auch Klappkarten wären denkbar. Das Design soll "das gewisse Etwas haben" und nicht zu verspielt sein.
Die Visitenkarten sind für die Firma KORVA, das Logo von der Ausstellung "raumfunke" soll dezent mit eingebunden werden (bei dem Briefpapier z.B. in der Fußzeile". Die farbliche Gestaltung sollte sich an den Farben des Logos orientieren.
Schriftart für Texte: Century Gothic
Schriftfarbe: RAL 7016
Nur eine Idee: Ich könnte mir auch gut vorstellen, dass die Visitenkarte aus einer Zündholzverpackung (wenn dann aber eine besondere mit nur einem Zündholz oder einem besonders breiten) besteht: http://glimmvelo.de/produkte_briefchen.php

```html
<!DOCTYPE html>
<html lang="de">
<head>
<meta charset="utf-8">
<title>KORVA – Visitenkarte</title>
<link rel="stylesheet" href="https://fonts.googleapis.com/css2?family=Questrial&display=swap">
<style>
  :root {
    --backdrop: #bf9a5c;
    --card: #152426;
    --text-grey: #6f7274;
    --logo-grey: #55595b;
    --flame-orange: #ff7300;
    --partner-grey: #8a8d8f;
  }
  * { margin: 0; padding: 0; box-sizing: border-box; }
  html, body {
    width: 1200px;
    height: 1120px;
    overflow: hidden;
    background: var(--backdrop);
    font-family: "Questrial", sans-serif;
  }
  .canvas { position: relative; width: 1200px; height: 1120px; }
  .card {
    position: absolute;
    left: 271px;
    width: 603px;
    height: 390px;
    background: var(--card);
    color: var(--text-grey);
  }
  .card--front { top: 112px; }
  .card--back { top: 571px; }

  .brand { position: absolute; left: 25px; top: 24px; }
  .brand__name {
    font-size: 70px;
    line-height: 1;
    letter-spacing: 2px;
    color: var(--logo-grey);
  }
  .brand__tagline {
    margin-top: 4px;
    font-size: 20px;
    color: var(--logo-grey);
  }

  .person { position: absolute; right: 25px; top: 184px; text-align: right; }
  .person__name { font-size: 33px; line-height: 1.1; }
  .person__role { font-size: 14px; margin-top: 4px; }

  .address {
    position: absolute; left: 25px; top: 254px;
    font-size: 21px; letter-spacing: 2px; line-height: 24px;
  }
  .address__city span { margin-left: 24px; }

  .phones {
    position: absolute; left: 25px; top: 310px;
    font-size: 17px; line-height: 21px;
  }
  .phones dt { display: inline-block; width: 49px; }
  .phones dd { display: inline; }

  .email, .web {
    position: absolute; bottom: 14px;
    font-size: 15px; letter-spacing: 1.6px;
  }
  .email { left: 24px; }
  .web { right: 20px; }

  .back__mark {
    position: absolute; left: 0; right: 0; top: 150px;
    text-align: center;
    font-size: 80px;
    letter-spacing: 4px;
    color: var(--flame-orange);
  }
  .partner {
    position: absolute; right: 17px; bottom: 18px;
    font-size: 21px;
    color: var(--partner-grey);
  }
</style>
</head>
<body>
<main class="canvas">
  <section class="card card--front">
    <div class="brand">
      <div class="brand__name">KORVA</div>
      <div class="brand__tagline">kamine · öfen · fliesen</div>
    </div>
    <div class="person">
      <div class="person__name">Henrik Korva</div>
      <div class="person__role">Geschäftsführer</div>
    </div>
    <address class="address" style="font-style:normal">
      <div>Am Lindenhang 5c</div>
      <div class="address__city">34511<span>Wendaburg</span></div>
    </address>
    <dl class="phones">
      <div><dt>fon:</dt><dd>05642 / 71 38 40</dd></div>
      <div><dt>fax:</dt><dd>05642 / 71 38 48</dd></div>
    </dl>
    <div class="email">info@korva-wendaburg.de</div>
    <div class="web">www.korva-wendaburg.de</div>
  </section>

  <section class="card card--back">
    <div class="back__mark">KORVA</div>
    <div class="partner">raumfunke</div>
  </section>
</main>
</body>
</html>
```